Carpentry framing business card and logo design

We need a logo that works well with baseball caps, tee shirts and sweat shirts. We are a carpentry framing company specializing in apartment complexes and large residential communities. We work in what is known as the tri state area southeastern Pennsylvania , New Jersey and northern Delaware . We would like to see die signs using the old English letter M and royal blue colors. Also we stress OSHA compliance and safety.

Industry/Entity Type

Residential

Contact Information for Business Card

Valdrick Construction Co Inc
4870 Quillford Lane
Ambler PA 19087
Dale Valdrick
dale1valdrick@norvexmail.com
267-815-0926

```html
<!DOCTYPE html>
<html lang="en">
<head>
<meta charset="utf-8">
<title>Valdrick Construction Co Inc – Business Card</title>
<link href="https://fonts.googleapis.com/css2?family=Tinos&family=Arimo&display=swap" rel="stylesheet">
<style>
  :root {
    --backdrop: #e9e6e2;
    --card: #ffffff;
    --ink: #1f1f1f;
    --accent: #a8262b;
    --mark: #a3a3a3;
    --rule: #1a1a1a;
  }
  html, body {
    margin: 0;
    padding: 0;
    width: 1200px;
    height: 818px;
    overflow: hidden;
    background: var(--backdrop);
  }
  .canvas {
    width: 1200px;
    height: 818px;
    display: flex;
    align-items: center;
    justify-content: center;
  }
  .card {
    position: relative;
    width: 1050px;
    height: 600px;
    background: var(--card);
    box-shadow: 0 6px 24px rgba(0,0,0,0.12);
  }
  .brand {
    position: absolute;
    left: 90px;
    top: 380px;
    display: flex;
    align-items: center;
    gap: 20px;
  }
  .brand-square {
    flex: none;
    width: 28px;
    height: 28px;
    background: var(--mark);
  }
  .brand-name {
    margin: 0;
    font-family: "Tinos", serif;
    font-weight: 400;
    font-size: 40px;
    line-height: 1.1;
    text-align: center;
    color: var(--ink);
  }
  .holder-name {
    position: absolute;
    left: 520px;
    top: 80px;
    margin: 0;
    font-family: "Tinos", serif;
    font-weight: 400;
    font-size: 36px;
    color: var(--accent);
  }
  .divider {
    position: absolute;
    left: 480px;
    top: 160px;
    width: 400px;
    height: 2px;
    background: var(--rule);
  }
  .icon-row {
    position: absolute;
    right: 50px;
    top: 150px;
    display: flex;
    gap: 14px;
  }
  .icon-row svg {
    width: 22px;
    height: 22px;
    fill: var(--accent);
  }
  .contact {
    position: absolute;
    right: 80px;
    top: 220px;
    margin: 0;
    padding: 0;
    list-style: none;
    font-family: "Arimo", sans-serif;
    font-size: 26px;
    line-height: 40px;
    text-align: right;
    color: var(--ink);
  }
</style>
</head>
<body>
<main class="canvas">
  <section class="card">
    <h2 class="holder-name">Dale Valdrick</h2>
    <div class="divider" aria-hidden="true"></div>

    <div class="icon-row" aria-hidden="true">
      <svg viewBox="0 0 24 24"><path d="M6.6 10.8a15.2 15.2 0 0 0 6.6 6.6l2.2-2.2c.3-.3.7-.4 1-.2 1.1.4 2.3.6 3.6.6.6 0 1 .4 1 1V20c0 .6-.4 1-1 1A17 17 0 0 1 3 4c0-.6.4-1 1-1h3.5c.6 0 1 .4 1 1 0 1.3.2 2.5.6 3.6.1.3 0 .7-.2 1z"/></svg>
      <svg viewBox="0 0 24 24"><path d="M2 5h20v14H2z M4 7v.5l8 5 8-5V7l-8 5z" fill-rule="evenodd"/></svg>
      <svg viewBox="0 0 24 24"><path d="M12 2a7 7 0 0 0-7 7c0 5 7 13 7 13s7-8 7-13a7 7 0 0 0-7-7zm0 9.5A2.5 2.5 0 1 1 12 6.5a2.5 2.5 0 0 1 0 5z"/></svg>
    </div>

    <ul class="contact">
      <li>267-815-0926</li>
      <li>dale1valdrick@norvexmail.com</li>
      <li>4870 Quillford Lane Corlanby PA 19087</li>
    </ul>

    <div class="brand">
      <span class="brand-square" aria-hidden="true"></span>
      <h1 class="brand-name">Valdrick Construction<br>Co Inc</h1>
    </div>
  </section>
</main>
</body>
</html>
```